design a construction company business card

Design business card around our logo. Card must have all the typical info: name, title, address, phone, email, business name, etc. Somewhere on the card I would like to see our motto "Built on integrity... Inspired by commitment." Consider adding a splash of bright orange to the card to complement the blues and silvers/grays in the logo. We are open to metallic inks, textures, etc. We would like to see options on both light and dark backgrounds. The font in the logo is Euro Technic Extended Regular.

```html
<!DOCTYPE html>
<html lang="en">
<head>
<meta charset="UTF-8">
<title>Halden Contracting – Business Card</title>
<link href="https://fonts.googleapis.com/css2?family=Oxygen:wght@400;700&display=swap" rel="stylesheet">
<style>
  :root {
    --page-bg: #e9e6e1;
    --card-dark: #2f2f31;
    --card-light: #ffffff;
    --brand-blue: #1f63b0;
    --brand-blue-deep: #17509a;
    --accent-orange: #ee6a24;
    --text-dark: #2b2b2b;
    --text-light: #ffffff;
  }
  * { box-sizing: border-box; margin: 0; padding: 0; }
  html, body {
    width: 1200px; height: 900px; overflow: hidden;
    background: var(--page-bg);
    font-family: "Oxygen", "Helvetica Neue", Arial, sans-serif;
  }
  .canvas { position: relative; width: 1200px; height: 900px; }

  .card {
    position: absolute; left: 280px; width: 640px; height: 366px;
    border-radius: 4px; overflow: hidden;
    box-shadow: 0 10px 28px rgba(0,0,0,.18);
  }

  /* Front (dark) */
  .card--front { top: 60px; background: var(--card-dark); }
  .front-brand {
    position: absolute; left: 150px; top: 118px;
    display: flex; align-items: center; gap: 14px;
  }
  .brand-square { width: 22px; height: 22px; background: var(--brand-blue); }
  .front-brand .brand-name {
    color: var(--brand-blue); font-weight: 700; font-size: 34px; letter-spacing: 2px;
  }
  .motto-rule {
    position: absolute; height: 1.5px; background: var(--accent-orange);
  }
  .motto-rule--top { left: 230px; top: 182px; width: 330px; }
  .motto-rule--bottom { left: 140px; top: 246px; width: 330px; }
  .motto {
    position: absolute; left: 168px; top: 203px;
    color: var(--accent-orange); font-size: 17px; letter-spacing: 1px;
  }

  /* Back (light) */
  .card--back { top: 476px; background: var(--card-light); }
  .name-marker {
    position: absolute; left: 0; top: 26px; width: 8px; height: 28px; background: var(--brand-blue);
  }
  .person-name {
    position: absolute; left: 48px; top: 24px;
    color: var(--brand-blue); font-size: 24px; letter-spacing: 1px;
  }
  .person-name strong { font-weight: 700; }
  .person-title {
    position: absolute; left: 38px; top: 58px;
    color: var(--text-dark); font-size: 15px; letter-spacing: .5px;
  }
  .person-title span { color: var(--brand-blue); }
  .contact-list {
    position: absolute; left: 20px; top: 118px; list-style: none;
  }
  .contact-list li {
    display: flex; align-items: center; gap: 10px;
    color: var(--text-dark); font-size: 16px; letter-spacing: .6px; height: 24px;
  }
  .contact-list svg { width: 16px; height: 16px; fill: var(--brand-blue); flex: none; }
  .back-brand {
    position: absolute; right: 48px; top: 124px;
    display: flex; align-items: center; gap: 10px;
  }
  .back-brand .brand-name {
    color: var(--brand-blue); font-weight: 700; font-size: 26px; letter-spacing: 1.5px;
  }
  .back-brand .brand-square { width: 16px; height: 16px; }
  .swoosh { position: absolute; left: 0; top: 0; width: 640px; height: 366px; }
  .address {
    position: absolute; left: 36px; top: 300px;
    color: var(--text-light); font-size: 15px; letter-spacing: .8px;
  }
</style>
</head>
<body>
<main class="canvas">

  <section class="card card--front" aria-label="Card front">
    <div class="front-brand">
      <div class="brand-square"></div>
      <div class="brand-name">HALDEN CONTRACTING</div>
    </div>
    <div class="motto-rule motto-rule--top"></div>
    <p class="motto">Built on Integrity... Inspired by Commitment</p>
    <div class="motto-rule motto-rule--bottom"></div>
  </section>

  <section class="card card--back" aria-label="Card back">
    <svg class="swoosh" viewBox="0 0 640 366" aria-hidden="true">
      <path d="M0,246 C220,236 450,280 640,366 L0,366 Z" fill="#1f63b0"/>
      <path d="M0,240 C220,230 450,274 640,362" fill="none" stroke="#ee6a24" stroke-width="5"/>
    </svg>

    <div class="name-marker"></div>
    <h1 class="person-name"><strong>MARCUS</strong> REED</h1>
    <p class="person-title">CEO of <span>Halden Contracting, INC</span></p>

    <ul class="contact-list">
      <li>
        <svg viewBox="0 0 24 24"><path d="M6.6 10.8a15.1 15.1 0 0 0 6.6 6.6l2.2-2.2a1 1 0 0 1 1-.25 11.4 11.4 0 0 0 3.6.57 1 1 0 0 1 1 1V20a1 1 0 0 1-1 1A17 17 0 0 1 3 4a1 1 0 0 1 1-1h3.5a1 1 0 0 1 1 1c0 1.25.2 2.45.57 3.57a1 1 0 0 1-.25 1z"/></svg>
        (02) 9555 0142
      </li>
      <li>
        <svg viewBox="0 0 24 24"><path d="M7 2h10a2 2 0 0 1 2 2v16a2 2 0 0 1-2 2H7a2 2 0 0 1-2-2V4a2 2 0 0 1 2-2zm0 3v13h10V5zm5 14.2a1 1 0 1 0 0 .01z"/></svg>
        0400 555 218
      </li>
      <li>
        <svg viewBox="0 0 24 24"><path d="M2 5h20v14H2zm2 2v.4l8 5.2 8-5.2V7zm0 2.8V17h16V9.8l-8 5.2z"/></svg>
        info@haldencontracting.com
      </li>
      <li>
        <svg viewBox="0 0 24 24"><path d="M12 2a10 10 0 1 0 0 20 10 10 0 0 0 0-20zm0 2c.9 1.2 1.6 2.9 1.9 5h-3.8c.3-2.1 1-3.8 1.9-5zM4.3 11h3.8a15 15 0 0 0 0 2H4.3a8 8 0 0 1 0-2zm5.8 0h3.8a13 13 0 0 1 0 2h-3.8a13 13 0 0 1 0-2zm5.8 0h3.8a8 8 0 0 1 0 2h-3.8a15 15 0 0 0 0-2zM12 20c-.9-1.2-1.6-2.9-1.9-5h3.8c-.3 2.1-1 3.8-1.9 5z"/></svg>
        www.haldencontracting.com
      </li>
    </ul>

    <div class="back-brand">
      <div class="brand-square"></div>
      <div class="brand-name">HALDEN</div>
    </div>

    <p class="address">12/7 Alder St, Westmead NSW 2145, NY</p>
  </section>

</main>
</body>
</html>
```